Winter is coming, is your home ready ?

We are a full service Insulation contracting services company . We insulate new and existing homes, commercial and industrial buildings.

We are looking for a billboard that shows our harsh winter approaching and a call to action for getting a free estimate.

We specialize in spray foam insulation but it doesn't need to be called out on the billboard if too much text make it looks too busy.

We do enjoy humor if its something that could work and keep people thinking of us.
Company web site is www.brambowinsulation.com
Company phone number is 555-318-2947

```html
<!DOCTYPE html>
<html lang="en">
<head>
<meta charset="utf-8">
<title>Brambow Insulation – Winter Billboard</title>
<link href="https://fonts.googleapis.com/css2?family=Montserrat:ital,wght@0,600;1,800&family=Oswald:wght@400;600&display=swap" rel="stylesheet">
<style>
  :root {
    --lime: #a8c022;
    --slate: #6a6b6e;
    --slate-dark: #5e5f62;
    --paper: #eeeeee;
    --paper-deep: #e2e2e2;
    --white: #ffffff;
    --page: #f4f5f7;
  }
  * { box-sizing: border-box; margin: 0; padding: 0; }
  html, body { width: 1115px; height: 1200px; overflow: hidden; background: var(--page); }
  .stage { position: relative; width: 1115px; height: 1200px; }
  .billboard {
    position: absolute; left: 20px; top: 411px;
    width: 1632px; height: 572px;
    transform: scale(0.6587); transform-origin: top left;
    background: linear-gradient(180deg, var(--paper) 0%, var(--paper-deep) 100%);
    box-shadow: 0 6px 14px rgba(0,0,0,0.25);
    overflow: hidden;
  }
  .accent-bar { position: absolute; left: 0; top: 0; width: 42px; height: 100%; background: var(--lime); }
  .brand { position: absolute; left: 93px; top: 40px; width: 590px; }
  .brand-row { display: flex; align-items: center; gap: 24px; height: 130px; }
  .brand-mark { width: 110px; height: 110px; background: var(--slate); flex: none; }
  .brand-name {
    font-family: "Montserrat", sans-serif; font-weight: 600;
    font-size: 64px; color: var(--slate); letter-spacing: 1px; line-height: 1;
  }
  .brand-rule { height: 4px; background: var(--lime); margin-top: 10px; }
  .brand-sub {
    font-family: "Montserrat", sans-serif; font-weight: 600; color: var(--slate);
    font-size: 34px; letter-spacing: 20px; margin-top: 14px; white-space: nowrap;
  }
  .headline-band {
    position: absolute; left: 42px; top: 268px; width: 740px; height: 127px;
    background: var(--slate); padding: 12px 0 0 52px;
  }
  .headline {
    font-family: "Montserrat", sans-serif; font-style: italic; font-weight: 800;
    font-size: 44px; line-height: 50px; color: var(--white); text-transform: uppercase;
  }
  .headline em { font-style: italic; color: var(--lime); }
  .phone {
    position: absolute; left: 88px; top: 408px;
    font-family: "Oswald", sans-serif; font-weight: 600; font-size: 80px;
    color: var(--slate); letter-spacing: 3px; line-height: 1;
  }
  .web {
    position: absolute; left: 90px; top: 500px;
    font-family: "Oswald", sans-serif; font-weight: 400; font-size: 48px;
    color: var(--slate); line-height: 1; letter-spacing: -1px; text-transform: uppercase;
  }
  .photo {
    position: absolute; left: 810px; width: 356px; border: 3px solid var(--lime);
  }
  .photo-terrace { top: 20px; height: 254px; background: linear-gradient(180deg, #f4f4f4 0%, #b46a52 55%, #e9ecef 100%); }
  .photo-house { top: 296px; height: 254px; background: linear-gradient(180deg, #f2f2f2 0%, #d9b36e 50%, #3f5a3c 78%, #eef0f2 100%); }
  .services {
    position: absolute; left: 1190px; top: 0; width: 420px; height: 100%;
    background: var(--slate); overflow: hidden;
  }
  .service-list { list-style: none; position: absolute; left: 66px; top: 52px; }
  .service-list li {
    display: flex; align-items: center; gap: 12px;
    font-family: "Oswald", sans-serif; font-weight: 400; font-size: 48px;
    color: var(--white); line-height: 58px; text-transform: uppercase;
  }
  .service-list li::before {
    content: ""; width: 22px; height: 22px; border-radius: 50%; background: var(--white);
  }
  .badge-circle {
    position: absolute; left: 158px; top: 280px; width: 300px; height: 300px;
    border-radius: 50%; background: var(--lime);
  }
  .margin-strip { position: absolute; left: 1610px; top: 0; width: 22px; height: 100%; background: var(--white); }
</style>
</head>
<body>
<div class="stage">
  <section class="billboard" aria-label="Brambow Insulation winter billboard">
    <div class="accent-bar"></div>

    <div class="brand">
      <div class="brand-row">
        <div class="brand-mark"></div>
        <div class="brand-name">brambow</div>
      </div>
      <div class="brand-rule"></div>
      <div class="brand-sub">insulation, inc.</div>
    </div>

    <div class="headline-band">
      <h1 class="headline"><em>Winter</em> is coming, is<br>your <em>home ready?</em></h1>
    </div>

    <p class="phone">(555) 318-2947</p>
    <p class="web">www.brambowinsulation.com</p>

    <div class="photo photo-terrace" role="img" aria-label="Photo of red-brick terraced houses covered in snow with bare trees"></div>
    <div class="photo photo-house" role="img" aria-label="Photo of a yellow house with snowy roof and fir trees in winter"></div>

    <aside class="services">
      <ul class="service-list">
        <li>Residential</li>
        <li>Commercial</li>
        <li>Industrial</li>
      </ul>
      <div class="badge-circle"></div>
    </aside>
    <div class="margin-strip"></div>
  </section>
</div>
</body>
</html>
```